Larkmoor Home Works Sales Flyer

We want a sales flyer that outlines our companies strengths with Kitchen & Bath Remodeling. We would like highlight those aspects while also showcasing our ability to do decks and home additions. We want financing packages to be a big part of the flyer.

Target Market(s)

Residential Customers

Requirements
Must have
• Financing options
Highlight Kitchen & bath remodeling
Less subtle is our decks and home additions
Nice to have
• Keep within our logo colors-we are looking for informative flyers that leave homeowners eager to call us after a meeting

```html
<!DOCTYPE html>
<html lang="en">
<head>
<meta charset="utf-8">
<title>Larkmoor Home Works – Kitchen and Bath Remodeling Flyer</title>
<link href="https://fonts.googleapis.com/css2?family=Poppins:ital,wght@0,400;0,500;0,600;0,700;1,400&display=swap" rel="stylesheet">
<style>
  :root {
    --navy: #0e1a33;
    --navy-text: #1c2a48;
    --orange: #f0562a;
    --red: #c8361f;
    --blue: #2a6bc0;
    --blue-deep: #1d4f99;
    --paper: #f2f2f1;
    --backdrop: #e6e6e4;
    --white: #ffffff;
    --body-text: #2b2b2b;
  }
  html, body {
    margin: 0;
    padding: 0;
    width: 1068px;
    height: 1200px;
    overflow: hidden;
    background: var(--backdrop);
  }
  .flyer {
    position: absolute;
    left: 117px;
    top: 10px;
    width: 834px;
    height: 1180px;
    display: block;
    box-shadow: 0 6px 20px rgba(0,0,0,0.18);
  }
  .flyer text { font-family: 'Poppins', sans-serif; }
  .brand-name { fill: var(--orange); font-weight: 600; font-size: 34px; letter-spacing: 1px; }
  .headline { font-weight: 700; font-size: 84px; }
  .headline-orange { fill: var(--orange); }
  .headline-navy { fill: var(--navy-text); }
  .headline-blue { fill: var(--blue); }
  .intro { fill: var(--body-text); font-size: 27px; font-weight: 400; }
  .services-title { fill: var(--white); font-weight: 700; font-size: 50px; }
  .service-name { fill: var(--white); font-weight: 600; font-size: 28px; }
  .service-text { fill: var(--white); font-size: 17px; font-style: italic; }
  .contact-text { fill: var(--white); font-weight: 600; font-size: 24px; }
</style>
</head>
<body>
<svg class="flyer" viewBox="0 0 1149 1625" xmlns="http://www.w3.org/2000/svg">
  <defs>
    <linearGradient id="grad-blue" x1="0" y1="0" x2="1" y2="1">
      <stop offset="0" stop-color="#2f78d0"/>
      <stop offset="1" stop-color="#1b4a93"/>
    </linearGradient>
    <linearGradient id="grad-orange" x1="0" y1="0" x2="1" y2="0">
      <stop offset="0" stop-color="#c8361f"/>
      <stop offset="0.4" stop-color="#f0562a"/>
      <stop offset="1" stop-color="#c8361f"/>
    </linearGradient>
    <linearGradient id="grad-kitchen" x1="0" y1="0" x2="1" y2="1">
      <stop offset="0" stop-color="#e9dccb"/>
      <stop offset="0.5" stop-color="#a4714a"/>
      <stop offset="1" stop-color="#4b3124"/>
    </linearGradient>
    <linearGradient id="grad-white-kitchen" x1="0" y1="0" x2="0" y2="1">
      <stop offset="0" stop-color="#ece8e2"/>
      <stop offset="0.6" stop-color="#d4cbc0"/>
      <stop offset="1" stop-color="#6a4a35"/>
    </linearGradient>
    <linearGradient id="grad-dark-bath" x1="0" y1="0" x2="1" y2="1">
      <stop offset="0" stop-color="#3c4442"/>
      <stop offset="1" stop-color="#1e2423"/>
    </linearGradient>
    <linearGradient id="grad-brick-bath" x1="0" y1="0" x2="0" y2="1">
      <stop offset="0" stop-color="#9a5238"/>
      <stop offset="0.6" stop-color="#7c3f2c"/>
      <stop offset="1" stop-color="#c9ccd0"/>
    </linearGradient>
    <linearGradient id="grad-footer" x1="0" y1="0" x2="1" y2="0">
      <stop offset="0" stop-color="#1d4f99"/>
      <stop offset="0.5" stop-color="#2a6bc0"/>
      <stop offset="1" stop-color="#1d4f99"/>
    </linearGradient>
  </defs>

  <rect class="flyer-base" width="1149" height="1625" fill="var(--navy)"/>

  <text class="brand-name" x="262" y="175" text-anchor="middle">LARKMOOR HOME WORKS</text>

  <polygon role="img" aria-label="Photo of a remodeled kitchen with wooden cabinets and island seating"
           points="530,0 1149,0 1149,430 856,590 530,410" fill="url(#grad-kitchen)"/>

  <polygon class="accent-blue" points="856,615 1149,452 1149,815" fill="url(#grad-blue)"/>
  <polygon class="accent-blue" points="0,232 96,295 0,355" fill="url(#grad-blue)"/>
  <polygon class="accent-orange" points="0,355 201,243 856,618 828,640 260,313 0,465" fill="url(#grad-orange)"/>
  <polygon class="accent-blue" points="0,815 260,965 330,965 0,1150" fill="url(#grad-blue)"/>

  <polygon class="accent-orange" points="520,818 856,632 856,1008" fill="url(#grad-orange)"/>
  <polygon class="accent-blue" points="856,1008 1149,840 1149,872 856,1030" fill="url(#grad-blue)"/>

  <polygon role="img" aria-label="Photo of a bright white kitchen with a wood counter and wire stools"
           points="556,815 856,650 1149,812 1149,830 856,990" fill="url(#grad-white-kitchen)"/>

  <polygon class="accent-blue" points="165,1015 521,808 870,1010 521,1222" fill="url(#grad-blue)"/>

  <polygon role="img" aria-label="Photo of a dark modern bathroom with shower and vanity mirror"
           points="221,1015 521,843 816,1015 521,1185" fill="url(#grad-dark-bath)"/>

  <polygon class="headline-panel" points="0,465 260,313 828,640 260,965 0,815" fill="var(--paper)"/>

  <polygon role="img" aria-label="Photo of a bathroom with brick tile wall and white double vanity"
           points="0,1040 116,985 536,1220 536,1515 0,1515" fill="url(#grad-brick-bath)"/>

  <text class="headline" x="61" y="512"><tspan class="headline-orange">Kitchen</tspan></text>
  <text class="headline" x="61" y="602"><tspan class="headline-navy">and </tspan><tspan class="headline-blue">Bath</tspan></text>
  <text class="headline headline-navy" x="61" y="692">Remodeling</text>
  <rect class="headline-rule" x="66" y="718" width="100" height="11" fill="var(--navy-text)"/>

  <text class="intro" x="66" y="777">Fresh kitchens and baths,</text>
  <text class="intro" x="66" y="812">plus decks and additions,</text>
  <text class="intro" x="84" y="847">with easy financing</text>
  <text class="intro" x="144" y="881">for every budget</text>

  <polygon class="services-banner" points="591,1195 726,1070 1149,1070 1149,1195" fill="url(#grad-orange)"/>
  <polygon class="services-banner-edge" points="591,1195 1149,1195 1149,1210 580,1210" fill="var(--red)"/>
  <text class="services-title" x="886" y="1140" text-anchor="middle">Services</text>

  <g class="service-item">
    <polygon points="659,1213 695,1249 659,1285 623,1249" fill="var(--white)"/>
    <text x="659" y="1259" text-anchor="middle" font-size="28" font-weight="700" fill="var(--navy)">$</text>
    <text class="service-name" x="721" y="1240">Flexible Financing</text>
    <text class="service-text" x="722" y="1267">Low monthly payments and 0% intro plans</text>
    <text class="service-text" x="722" y="1288">for qualified homeowners. Ask us today.</text>
  </g>
  <g class="service-item">
    <polygon points="659,1311 695,1347 659,1383 623,1347" fill="var(--white)"/>
    <rect x="643" y="1336" width="32" height="4" fill="var(--navy)"/>
    <rect x="643" y="1343" width="32" height="4" fill="var(--navy)"/>
    <rect x="643" y="1350" width="32" height="4" fill="var(--navy)"/>
    <rect x="646" y="1354" width="4" height="10" fill="var(--navy)"/>
    <rect x="668" y="1354" width="4" height="10" fill="var(--navy)"/>
    <text class="service-name" x="721" y="1338">Custom Decks</text>
    <text class="service-text" x="722" y="1363">Wood and composite decks built to last</text>
    <text class="service-text" x="722" y="1384">through every season of outdoor living.</text>
  </g>
  <g class="service-item">
    <polygon points="659,1405 695,1441 659,1477 623,1441" fill="var(--white)"/>
    <path d="M644,1442 l15,-13 l15,13 v14 h-30 z" fill="var(--navy)"/>
    <rect x="655" y="1447" width="8" height="9" fill="var(--white)"/>
    <text class="service-name" x="721" y="1430">Home Additions</text>
    <text class="service-text" x="722" y="1456">Extra bedrooms, sunrooms and more space</text>
    <text class="service-text" x="722" y="1477">designed to blend with your home.</text>
  </g>

  <rect class="footer-rule" x="0" y="1515" width="1149" height="9" fill="var(--red)"/>
  <rect class="footer-band" x="0" y="1524" width="1149" height="101" fill="url(#grad-footer)"/>

  <g class="contact-item">
    <polygon points="66,1551 84,1561 84,1581 66,1591 48,1581 48,1561" fill="var(--white)"/>
    <path d="M60,1562 q0,14 12,18 l3,-4 l-4,-3 l-2,2 q-4,-3 -5,-7 l2,-2 l-3,-4 z" fill="var(--blue-deep)"/>
    <text class="contact-text" x="111" y="1580">1234 567 890</text>
  </g>
  <g class="contact-item">
    <polygon points="327,1551 345,1561 345,1581 327,1591 309,1581 309,1561" fill="var(--white)"/>
    <circle cx="327" cy="1571" r="9" fill="none" stroke="var(--blue-deep)" stroke-width="2"/>
    <ellipse cx="327" cy="1571" rx="4" ry="9" fill="none" stroke="var(--blue-deep)" stroke-width="2"/>
    <line x1="318" y1="1571" x2="336" y2="1571" stroke="var(--blue-deep)" stroke-width="2"/>
    <text class="contact-text" x="371" y="1580">www.yourcompany.com</text>
  </g>
  <g class="contact-item">
    <polygon points="733,1551 751,1561 751,1581 733,1591 715,1581 715,1561" fill="var(--white)"/>
    <rect x="723" y="1564" width="20" height="14" fill="none" stroke="var(--blue-deep)" stroke-width="2"/>
    <path d="M723,1564 l10,8 l10,-8" fill="none" stroke="var(--blue-deep)" stroke-width="2"/>
    <text class="contact-text" x="776" y="1580">info@yourcompany.com</text>
  </g>
</svg>
</body>
</html>
```